business card deign

Logo needs the following on it.
1. attached logo
2. Tagline - "Cold drinks, loud tunes and a night that runs late!"
3. Name- Dalton Pikes, Founder and CPO
4. Address - 412 E. Carver Avenue, Ste 2207, Tampa, FL. 33917
5. Phone - 555.318.4726

```html
<!DOCTYPE html>
<html lang="en">
<head>
<meta charset="utf-8">
<title>Kestro Business Card</title>
<link rel="stylesheet" href="https://fonts.googleapis.com/css2?family=Montserrat:wght@400;600&family=Oswald:wght@500&display=swap">
<style>
  :root {
    --backdrop: #e6e6e8;
    --card: #242424;
    --ink-light: #ffffff;
    --ink-soft: #d6d6d6;
    --ink-dark: #101010;
    --art-top: #6e6e6e;
    --art-mid: #2a2a2a;
    --art-base: #141414;
  }
  * { margin: 0; padding: 0; box-sizing: border-box; }
  html, body { width: 1200px; height: 1108px; overflow: hidden; }
  body {
    background: var(--backdrop);
    font-family: "Montserrat", Arial, sans-serif;
    position: relative;
  }
  .card {
    position: absolute;
    width: 740px;
    height: 443px;
    background: var(--card);
    color: var(--ink-light);
  }
  .card--front { left: 241px; top: 68px; }
  .card--back { left: 248px; top: 589px; }

  .wordmark {
    position: absolute;
    font-family: "Oswald", "Arial Narrow", sans-serif;
    font-weight: 500;
    letter-spacing: 0.6em;
    line-height: 1;
  }
  .card--front .wordmark {
    left: 36px; top: 70px;
    font-size: 46px;
    color: var(--ink-light);
  }
  .holder { position: absolute; left: 35px; top: 174px; }
  .holder__name { font-size: 26px; font-weight: 600; line-height: 1.1; }
  .holder__role { font-size: 16px; color: var(--ink-soft); margin-top: 3px; }
  .address {
    position: absolute; left: 35px; top: 258px;
    font-size: 16px; line-height: 20px; color: var(--ink-soft);
  }
  .contacts {
    position: absolute; left: 36px; top: 320px;
    list-style: none; font-size: 16px; color: var(--ink-soft);
  }
  .contacts li { display: flex; align-items: center; height: 32px; }
  .contacts svg { width: 16px; height: 16px; margin-right: 9px; fill: var(--ink-light); }

  .mascot-art {
    position: absolute;
    background: radial-gradient(ellipse at 75% 20%, var(--art-top) 0%, var(--art-mid) 45%, var(--art-base) 100%);
    border-radius: 40% 50% 8px 8px;
    opacity: 0.85;
  }
  .card--front .mascot-art { left: 330px; top: 152px; width: 362px; height: 280px; }
  .card--back .mascot-art { left: 212px; top: 62px; width: 262px; height: 198px; }

  .card--back .wordmark {
    left: 0; right: 0; top: 272px;
    text-align: center;
    font-size: 46px;
    padding-left: 0.6em;
    color: var(--ink-dark);
  }
  .tagline {
    position: absolute; left: 0; right: 0; top: 387px;
    text-align: center; font-size: 16px; color: var(--ink-soft);
  }
</style>
</head>
<body>
  <section class="card card--front">
    <div class="wordmark">KESTRO</div>
    <div class="holder">
      <div class="holder__name">Dalton Pikes</div>
      <div class="holder__role">Founder and CPO</div>
    </div>
    <div class="address">412 E. Carver Avenue, Ste 2207,<br>Tampa, FL. 33917</div>
    <ul class="contacts">
      <li><svg viewBox="0 0 16 16" aria-hidden="true"><path d="M3.5 1.5l2.5 3-1.5 1.7a9 9 0 0 0 5.3 5.3L11.5 10l3 2.5-1.4 2.2C7 14.5 1.5 9 1.3 2.9z"/></svg>555.318.4726</li>
      <li><svg viewBox="0 0 16 16" aria-hidden="true"><path d="M1.5 3.5h13v1.2L8 8.7 1.5 4.7z M1.5 6.2L8 10.2l6.5-4v6.3h-13z"/></svg>info@kestro.com</li>
      <li><svg viewBox="0 0 16 16" aria-hidden="true"><path d="M8 1a7 7 0 1 0 0 14A7 7 0 0 0 8 1zm0 1.6a5.4 5.4 0 0 1 4.3 2.2H10.5L9 6.5l1 1.6-1.6 2.4.4 2.8A5.4 5.4 0 0 1 3.2 5.6l1.8.6 1.3 1.8L5.8 10l1.4.8V9l1.6-1.5L7.2 5.3 8.4 3z"/></svg>www.kestro.com</li>
    </ul>
    <div class="mascot-art" role="img" aria-label="Large dark glossy animal mascot silhouette decoration"></div>
  </section>

  <section class="card card--back">
    <div class="mascot-art" role="img" aria-label="Dark glossy animal mascot silhouette above the brand name"></div>
    <div class="wordmark">KESTRO</div>
    <p class="tagline">Cold drinks, loud tunes and a night that runs late</p>
  </section>
</body>
</html>
```